NEW Modern Sleek Business Card for VR Language Startup

Our startup is using VR to lead the next wave of world language education. We need a two-sided business card that introduces the larger organization (Brightloom Language Inc) and our contact info on one side and shows the product, Glimwoorld, on the other side.

Side 1 (contact info)= Brightloom Logo and Contact info (name, title, phone, email)

Side 2 (product)= Glimworld logo, text, and website
Text= Culturally Immersive Language Learning Games
Website= www.glimworld-play.com

Target Market(s)

Education, Technology

Contact Information for Business Card

Contact info will be updated upon approval of the design. For now, put this as a placeholder.

Perry Dunmore
Founder & CEO
pdunmore@quillpost-mail.net
(555)-014-2286

Font styles to use
Other font styles liked:
• Gibson and Century Gothic are the brand fonts

Requirements
Nice to have
• I would love to see cohesion between the design and colors of the two logos. I have attached a few business card designs that I like, so you can get a feel for my preferred style.

```html
<!DOCTYPE html>
<html lang="en">
<head>
<meta charset="utf-8">
<title>Glimworld Business Card</title>
<link rel="stylesheet" href="https://fonts.googleapis.com/css2?family=Mulish:wght@400;600;800&display=swap">
<style>
  :root {
    --stage: #2b2b2b;
    --card: #1a1a1a;
    --ink: #ffffff;
    --ink-soft: #e6e6e6;
    --silver: #d9d9d9;
  }
  * { margin: 0; padding: 0; box-sizing: border-box; }
  html, body { width: 1200px; height: 812px; overflow: hidden; }
  body {
    background: var(--stage);
    font-family: "Mulish", "Century Gothic", sans-serif;
    color: var(--ink);
    display: flex;
    align-items: center;
    justify-content: center;
    gap: 40px;
  }
  .card {
    position: relative;
    width: 540px;
    height: 309px;
    background: var(--card);
    box-shadow: 0 14px 30px rgba(0, 0, 0, 0.45);
  }
  .brand-dot {
    flex: none;
    border-radius: 50%;
  }

  /* Product side */
  .product-brand {
    position: absolute;
    top: 92px;
    left: 0;
    right: 0;
    display: flex;
    align-items: center;
    justify-content: center;
    gap: 12px;
  }
  .product-brand .brand-dot {
    width: 34px;
    height: 34px;
    background: var(--silver);
  }
  .product-brand .brand-name {
    font-size: 34px;
    font-weight: 800;
    color: var(--silver);
    letter-spacing: 0.5px;
  }
  .tagline {
    position: absolute;
    bottom: 72px;
    left: 0;
    right: 0;
    text-align: center;
    font-size: 14px;
    font-weight: 400;
    letter-spacing: 0.6px;
    color: var(--ink-soft);
  }
  .product-web {
    position: absolute;
    bottom: 48px;
    left: 0;
    right: 0;
    text-align: center;
    font-size: 12.5px;
    font-weight: 400;
    letter-spacing: 0.6px;
    color: var(--ink-soft);
  }

  /* Contact side */
  .contact-brand {
    position: absolute;
    left: 40px;
    bottom: 52px;
    width: 230px;
    display: flex;
    align-items: center;
    gap: 12px;
  }
  .contact-brand .brand-dot {
    width: 30px;
    height: 30px;
    background: var(--ink);
  }
  .contact-brand .brand-name {
    font-size: 23px;
    line-height: 1.15;
    font-weight: 800;
    color: var(--ink);
  }
  .contact-block {
    position: absolute;
    left: 300px;
    top: 64px;
  }
  .person-name {
    font-size: 25px;
    font-weight: 600;
    letter-spacing: 0.4px;
  }
  .person-title {
    font-size: 13px;
    font-weight: 400;
    color: var(--ink-soft);
    margin-top: 2px;
    margin-left: 12px;
  }
  .divider {
    width: 38px;
    height: 1px;
    background: var(--ink);
    margin: 12px 0 16px 22px;
  }
  .contact-list { list-style: none; margin-left: 24px; }
  .contact-list li {
    display: flex;
    align-items: center;
    gap: 10px;
    font-size: 12.5px;
    line-height: 1;
    margin-bottom: 8px;
    color: var(--ink-soft);
  }
  .contact-icon { width: 11px; height: 11px; flex: none; fill: var(--ink); }
</style>
</head>
<body>

  <section class="card card-product" aria-label="Product side">
    <div class="product-brand">
      <span class="brand-dot"></span>
      <span class="brand-name">Glimworld</span>
    </div>
    <p class="tagline">Culturally Immersive Language Learning Games</p>
    <p class="product-web">www.glimworld-play.com</p>
  </section>

  <section class="card card-contact" aria-label="Contact side">
    <div class="contact-brand">
      <span class="brand-dot"></span>
      <span class="brand-name">Brightloom<br>Language Inc</span>
    </div>
    <div class="contact-block">
      <h1 class="person-name">Perry Dunmore</h1>
      <p class="person-title">Founder &amp; CEO</p>
      <div class="divider"></div>
      <ul class="contact-list">
        <li>
          <svg class="contact-icon" viewBox="0 0 24 24" aria-hidden="true"><path d="M6.6 10.8a15.1 15.1 0 0 0 6.6 6.6l2.2-2.2a1 1 0 0 1 1-.25 11.4 11.4 0 0 0 3.6.57 1 1 0 0 1 1 1V20a1 1 0 0 1-1 1A17 17 0 0 1 3 4a1 1 0 0 1 1-1h3.5a1 1 0 0 1 1 1c0 1.25.2 2.45.57 3.6a1 1 0 0 1-.25 1z"/></svg>
          <span>(555)-014-2286</span>
        </li>
        <li>
          <svg class="contact-icon" viewBox="0 0 24 24" aria-hidden="true"><path d="M2 5h20v14H2z M2 5l10 8 10-8" fill="none" stroke="#fff" stroke-width="2.4"/></svg>
          <span>pdunmore@quillpost-mail.net</span>
        </li>
      </ul>
    </div>
  </section>

</body>
</html>
```